Brightmill Data Works

Our company is about IT hardwares and IT solutions. IT hardware such as PC, RAMS, storage and servers. IT solutions such as project management, BA. We are also selling new technology too.

Target Market(s)

Consumer, Small to Medium Business, Corporate

Requirements
Must have
• The business card must have the following:
• Name:
• Title:
• Contact Number:
• Email address:
• Website:
• Color: Must match the logo color upgrade

```html
<!DOCTYPE html>
<html lang="en">
<head>
<meta charset="utf-8">
<title>Brightmill Data Works – Business Card</title>
<link href="https://fonts.googleapis.com/css2?family=Arimo:wght@400;700&display=swap" rel="stylesheet">
<style>
  :root {
    --backdrop: #3b3430;
    --card: #1a1a1a;
    --card-edge: #101010;
    --silver: #b9b9b9;
    --orange: #e2861f;
    --white: #f4f4f4;
  }
  * { margin: 0; padding: 0; box-sizing: border-box; }
  html, body {
    width: 1200px;
    height: 780px;
    overflow: hidden;
    background: var(--backdrop);
    font-family: "Arimo", Arial, sans-serif;
  }
  .canvas {
    width: 1200px;
    height: 780px;
    display: flex;
    align-items: center;
    justify-content: center;
    gap: 40px;
  }
  .card {
    width: 540px;
    height: 310px;
    background: var(--card);
    border: 1px solid var(--card-edge);
    border-radius: 4px;
    box-shadow: 0 12px 30px rgba(0,0,0,0.45);
    position: relative;
    overflow: hidden;
  }

  /* Front */
  .card-front {
    display: flex;
    align-items: center;
    justify-content: center;
  }
  .front-name {
    display: flex;
    align-items: center;
    gap: 12px;
    color: var(--silver);
    font-weight: 700;
    font-size: 26px;
    letter-spacing: 1px;
    text-transform: uppercase;
  }
  .front-name .mark-square {
    width: 14px; height: 14px;
    background: var(--silver);
  }

  /* Back */
  .card-back {
    display: grid;
    grid-template-columns: 1fr 2px 1.15fr;
    align-items: center;
  }
  .brand {
    display: flex;
    flex-direction: column;
    align-items: center;
    gap: 10px;
    padding: 0 16px;
  }
  .brand .mark-square {
    width: 16px; height: 16px;
    background: var(--orange);
  }
  .brand-name {
    color: var(--white);
    font-weight: 700;
    font-size: 19px;
    letter-spacing: 0.5px;
    text-transform: uppercase;
    text-align: center;
    line-height: 1.25;
  }
  .divider {
    width: 1px;
    height: 150px;
    background: var(--orange);
    justify-self: center;
  }
  .contact {
    padding-left: 26px;
    color: var(--white);
  }
  .person-name {
    font-weight: 700;
    font-size: 17px;
    letter-spacing: 0.5px;
    text-transform: uppercase;
  }
  .person-title {
    color: var(--orange);
    font-size: 14px;
    margin-bottom: 12px;
  }
  .address {
    font-size: 14px;
    line-height: 1.35;
    margin-bottom: 4px;
  }
  .contact-line {
    display: flex;
    align-items: center;
    gap: 7px;
    font-size: 14px;
    line-height: 1.45;
  }
  .contact-line svg {
    width: 11px; height: 11px;
    flex: none;
  }
</style>
</head>
<body>
<main class="canvas">
  <section class="card card-front" aria-label="Card front">
    <div class="front-name"><span class="mark-square"></span>Brightmill</div>
  </section>

  <section class="card card-back" aria-label="Card back">
    <div class="brand">
      <span class="mark-square"></span>
      <div class="brand-name">Brightmill<br>Data Works</div>
    </div>
    <div class="divider"></div>
    <div class="contact">
      <div class="person-name">Dara Keller</div>
      <div class="person-title">Manager</div>
      <div class="address">PO Box 480 Harbour Lane,<br>Larkfield</div>
      <div class="contact-line">
        <svg viewBox="0 0 12 12" aria-hidden="true"><path fill="#e2861f" d="M2 1h2.5l1 2.5-1.5 1a6 6 0 0 0 3.5 3.5l1-1.5 2.5 1V10a1 1 0 0 1-1 1A9 9 0 0 1 1 2a1 1 0 0 1 1-1z"/></svg>
        555-204-7781
      </div>
      <div class="contact-line">
        <svg viewBox="0 0 12 12" aria-hidden="true"><rect x="0.5" y="2" width="11" height="8" fill="#e2861f"/><path d="M0.5 2.5 6 6.5l5.5-4" fill="none" stroke="#1a1a1a" stroke-width="1"/></svg>
        hello@brightmilldata.com
      </div>
      <div class="contact-line">
        <svg viewBox="0 0 12 12" aria-hidden="true"><circle cx="6" cy="6" r="5.5" fill="#e2861f"/><path d="M0.5 6h11M6 0.5c-3 3-3 8 0 11M6 0.5c3 3 3 8 0 11" fill="none" stroke="#1a1a1a" stroke-width="0.8"/></svg>
        www.brightmilldata.com
      </div>
    </div>
  </section>
</main>
</body>
</html>
```